Buch-/eBook-Cover für Traumatherapeutin
Zielgruppe
Ich bin Traumatherapeutin und schreibe ein Buch zum Thema Trauma bearbeiten.
Meine Zielgruppe sucht Heilung, Genesung, Selbstliebe etc.
Aufgabenstellung
Buchcover
Bitte erstell mir ein modernes positives inspirierendes Buchcover mit dem
Titel: 'Morgenlicht NEU entdecken“
Untertitel: „Spüre den Mut der ganz in dir wohnt“
Dr. Mira Kessow
Ich hätte gerne ein modernes Buch, das entweder einen Bezug zum Thema Trauma hat oder aber einfach stylische Schriftzüge. Bin aber auch offen für andere Vorschläge.
Dunkelblau, weiß und türkis oder auch rosa mag ich ganz gerne. Wobei Dunkelblau, weiß und türkis meine Favoriten sind und mit rosa höchstens kleinere Akzente gesetzt werden sollten.
Das Buchcover soll modern sein und direkt ansprechen. Gerne eine originelle Lösung, oder etwas Besonderes, etwas das Tiefe ausdrückt, oder man mehrmals hinsehen muss um etwas zu erkennen oder etwas das mehr Interpretationsspielraum lässt.
Gerne auch viel weiß, zumindest heller und nicht zu dunkel. Stylish, aber nicht überfrachtet.
Schreib mich gerne an, wenn du Fragen hast.
Ich habe mal zwei Beispiel von Typolösungen angehängt, die ich ganz cool fände.
Ich freue mich auf deine Ideen :-)
Ganz liebe Grüße
Mira

```html
<!DOCTYPE html>
<html lang="de">
<head>
<meta charset="utf-8">
<title>Morgenlicht NEU entdecken – Dr. Mira Kessow</title>
<link href="https://fonts.googleapis.com/css2?family=Bebas+Neue&family=Roboto:wght@400&family=Satisfy&display=swap" rel="stylesheet">
<style>
  :root {
    --teal: #4fb8a5;
    --gold-light: #d2bf40;
    --gold-dark: #a78f1c;
    --paper: #ffffff;
    --lavender: #e4e8f5;
    --mint: #a9dccc;
    --navy: #2e3461;
  }
  html, body {
    margin: 0;
    padding: 0;
    width: 750px;
    height: 1200px;
    overflow: hidden;
    background: var(--paper);
  }
  .cover {
    position: relative;
    width: 750px;
    height: 1200px;
    background: var(--paper);
    overflow: hidden;
  }
  .author {
    position: absolute;
    top: 40px;
    left: 0;
    width: 100%;
    text-align: center;
    font-family: "Bebas Neue", sans-serif;
    font-size: 40px;
    line-height: 1;
    color: var(--teal);
    letter-spacing: 0.5px;
  }
  .title-top,
  .title-bottom {
    position: absolute;
    left: 0;
    width: 100%;
    text-align: center;
    font-family: "Bebas Neue", sans-serif;
    color: var(--teal);
    line-height: 1;
    margin: 0;
    font-weight: 400;
  }
  .title-top {
    top: 106px;
    font-size: 158px;
    letter-spacing: 1px;
  }
  .title-bottom {
    top: 415px;
    font-size: 174px;
    letter-spacing: 2px;
  }
  .title-script {
    position: absolute;
    top: 170px;
    left: 0;
    width: 100%;
    text-align: center;
    font-family: "Satisfy", cursive;
    font-size: 230px;
    line-height: 1;
    background: linear-gradient(100deg, var(--gold-light) 0%, var(--gold-dark) 45%, var(--gold-light) 70%, var(--gold-light) 100%);
    -webkit-background-clip: text;
    background-clip: text;
    color: transparent;
    z-index: 2;
  }
  .subtitle {
    position: absolute;
    top: 574px;
    left: 0;
    width: 100%;
    text-align: center;
    font-family: "Roboto", sans-serif;
    font-size: 33px;
    color: var(--teal);
    margin: 0;
    font-weight: 400;
  }
  .illustration {
    position: absolute;
    left: 140px;
    top: 640px;
    width: 470px;
    height: 530px;
    border-radius: 48% 48% 18% 18% / 30% 30% 10% 10%;
    background:
      radial-gradient(ellipse at 50% 78%, rgba(46, 52, 97, 0.55) 0%, rgba(46, 52, 97, 0) 38%),
      radial-gradient(ellipse at 15% 70%, var(--mint) 0%, rgba(169, 220, 204, 0) 40%),
      radial-gradient(ellipse at 85% 60%, var(--mint) 0%, rgba(169, 220, 204, 0) 40%),
      var(--lavender);
  }
</style>
</head>
<body>
  <main class="cover">
    <p class="author">Dr. Mira Kessow</p>
    <h1 class="book-title">
      <span class="title-top">Morgenlicht</span>
      <span class="title-script">neu</span>
      <span class="title-bottom">Entdecken</span>
    </h1>
    <p class="subtitle">Spüre den Mut der ganz in dir wohnt</p>
    <div class="illustration" role="img" aria-label="Illustration: helle Silhouette eines Oberkörpers mit einer geöffneten Tür in der Brust, aus der eine kleine Frau ins Licht tritt, umrahmt von türkisen Blättern"></div>
  </main>
</body>
</html>
```